Nutritional & Gastrointestinal Health Consulting Service-Website design

We need a website design for a new health consulting service called "Bright Vale" based in Perth, Australia.

We will be providing consulting services in the areas of:
1) Nutrition and Diet
2) Gastrointestinal Health (which means stomach & digestive system related health)

These consulting services will be provided by an Accredited Dietitian and a Paediatric Gastroenterologist.

We are open to creative ideas in terms of design, layout, fonts and colours. We also would love to see images of nature in the backdrop with families (adults with kids) having a good time, fresh fruits and vegetables displayed in a farmer's market or supermarket. 2 or 3 images should be sufficient. We would also definitely want our logo somewhere in the main page of website. The logo file is also attached. Please have a look at a website's design that we really liked. We would love to see designs inspired by that style. The website details are in the in the "nice to have priorities" section of this project brief.

We also would be looking at website designers with software coding skills so that if we like the design we can go ahead with the next step of coding.

The website design should communicate the purpose of the website and at the same time be simple, elegant and unique/eye-catching.

We look forward to receiving creative ideas for our website from you all. Good luck!

More details have been added to our project- for example: Logo, fonts style, must haves etc etc. Please view the updated project brief. Looking forward to receiving your fantastic ideas for our website. Thanking you

Hi, I have updated the colour preference. Will add the content preferences tomorrow. thanks

Hello all, I have now added a LOT more content to what we want in our website. It is very much in detail, so please carefully have a read through the entire project brief. If you have any questions write back to me and I will try to respond as quickly as I can. Last few days were busy so couldn't respond quickly to all of you who had send me designs/queries/questions. Thank you for your patience. I look forward to receiving fantastic designs from you all. Good Luck :-)

Target Market(s)

Adults based in western speaking countries aged 18 to 60 years

Industry/Entity Type

Software

Font styles to use
Sans Serif
Script

Colors
faa54b
acd036

Requirements
Must have
• The website must have the MAIN logo file attached. I have attached 3 files: 1) MAIN logo; 2) supplementary logo A ; 3) supplementary logo B

I have selected 2 colours from the colour scheme (see below)-(as the colour of our logo is that).
However we would also like to see LIGHT CHOCOLATE BROWN or CHOCOLATE BROWN colour used as the background colour of the website
Preferred WEBSITE CONTENT:
1) HOME PAGE:
Content required=
--Company Logo
--Dr Dorian Pelham
Paediatric Gastroenterologist & Hepatologist
-Marla Pelham.
Dietitian & Nutritionist
--Website Menu (either listed horizontally or vertically):
Once clicked on each name:

Under each of the Website Menu items we want the following Headings to be added

2) ABOUT US page:
Sub-heading under this: Qualification, Skills, Special Interest

3) SERVICES
DORIAN'S PAGE: Individual Consultation, Endoscopy procedures
Individual Consultation, Group Based Services, Food Diary, Food & Symptom Diary

4) FEES & REBATE: Content as below:
Please Note: Payment of full fees is required at the time of consultation and procedures. 48 hours notice is required for cancellation of appointments/non-attendance. Failure to provide this may result in a fee being incurred. Please call reception to find out the amount of fee charged for cancellation of appointments/non-attendance.
headings are:
Paediatric Gastroenterology:
Dorian's pge
Individual Consultation - Initial (upto 30 mins):
Review Consultation (upto 15 mins):
Endoscopy procedures - No Gap fees charged. Fees will be billed directly to Vitacover. If any queries, please contact reception.

marla's pge
sub heading:
Individual Consultation - Initial (upto 45 mins):
Individual Consultation - Review (upto 30 mins):

Concession-Individual Consultation -Initial (upto 45 mins):
Concession-Individual Consultation - Review (upto 30 mins):
Please Note: Concession applies for health care card holders & pensioners

Group Based Services: Pricing subject to the type of service provided. Please contact us for an obligation free quote.
Education Topics Include:
- Paediatric Nutrition (Introducing Solids, Fussy Eating, Healthy Eating)
- Pregnancy Nutrition, Gestational Diabetes, Breastfeeding/Lactation Nutrition
- Healthy Eating, Supermarket Shopping Tips, Nutrition Label Reading Tips, Healthier
sub heading under nutrition & diet:
-Vitacover:
--A rebate of $52.95 is available from Vitacover if an EPC ( Enhanced Primary Care)/Chronic Disease Management (CDM) plan is issued by your GP.
--All mandatory paperwork needs to be available at the time of making your appointment for your eligibility.
-Private Health Fund:
--Most private health funds provide rebate on dietetic appointments. However the rebate amount depends on your level of cover. Thus, please contact your health fund to determine your entitled rebate.
-RSB: Approved provider for RSB services

6) FOR DOCTORS: Bright Vale Paediatric Gastroenterologist Referral Form
Bright Vale Dietitian Referral form
7) LOCATIONS & CONTACT

Paediatric Gastroenterology & Hepatology Service
Suite 46
Holy Lantern Bramcote Medical Centre
17 Colin Ferris Pde,
MURDOCH, WA 6150
P: (08) 9422 5061
F: (08) 9422 3094

Nutrition & Diet Service
Suite 46
17 Colin Ferris Pde,
MURDOCH, WA 6150
P: (08) 9422 5061
F: (08) 9422 3094

Tolland Medical Centre
58-60 Karrigan Parkway,
MANDURAH, WA 6210
P: (08) 9647 2283
F: (08) 96724419
www.tmcexample.com.au

This page should have a webform that has following titles:
-Your Name
-Your Email
-Your Phone
-Message

8) NEWS & BLOG
Nice to have
• We liked the design style of the websites below:
https://www.vendoraplex.example/

http://qoravelt.example/

But feel free to use your creativity too
Should not have
• Please do not use any body building or muscle building images

```html
<!DOCTYPE html>
<html lang="en">
<head>
<meta charset="utf-8">
<title>Bright Vale</title>
<link rel="stylesheet" href="https://fonts.googleapis.com/css2?family=Open+Sans:wght@400;700;800&display=swap">
<style>
  :root {
    --brown-deep: #3f2420;
    --brown-mid: #55302a;
    --brown-light: #7b4a40;
    --band: rgba(20, 10, 8, 0.62);
    --orange: #faa54b;
    --green: #acd036;
    --white: #ffffff;
    --icon-cut: #2a1613;
  }
  html, body { margin: 0; padding: 0; overflow: hidden; }
  .page {
    position: relative;
    width: 1200px;
    height: 863px;
    overflow: hidden;
    font-family: "Open Sans", Arial, sans-serif;
    color: var(--white);
    background:
      radial-gradient(ellipse 700px 600px at 1120px 80px, var(--brown-light), transparent 70%),
      linear-gradient(160deg, var(--brown-deep) 0%, var(--brown-mid) 55%, #4c2b27 100%);
  }
  .practitioner {
    position: absolute;
    top: 211px;
    width: 360px;
    text-align: center;
    font-size: 14.5px;
    line-height: 21px;
  }
  .practitioner strong { font-weight: 800; }
  .practitioner--doctor { left: 135px; }
  .practitioner--dietitian { left: 685px; }

  .brand-dot {
    position: absolute;
    left: 545px;
    top: 300px;
    width: 110px;
    height: 110px;
    border-radius: 50%;
    background: var(--orange);
  }
  .menu-band {
    position: absolute;
    left: 0;
    top: 369px;
    width: 1200px;
    height: 126px;
    background: var(--band);
  }
  .menu { list-style: none; margin: 0; padding: 0; }
  .menu-item {
    position: absolute;
    top: 393px;
    width: 130px;
    margin-left: -65px;
    text-align: center;
    font-size: 13.5px;
    font-weight: 700;
    line-height: 15px;
    text-transform: uppercase;
  }
  .menu-icon {
    display: block;
    width: 30px;
    height: 30px;
    margin: 0 auto 12px;
  }
  .brand-name {
    position: absolute;
    left: 0;
    top: 528px;
    width: 1200px;
    margin: 0;
    text-align: center;
    font-size: 96px;
    line-height: 150px;
    font-weight: 800;
    letter-spacing: 3px;
    color: var(--green);
  }
</style>
</head>
<body>
<div class="page">
  <div class="practitioner practitioner--doctor">
    <strong>DR DORIAN</strong> PELHAM<br>Paediatric Gastroenterologist &amp; Hepatologist
  </div>
  <div class="practitioner practitioner--dietitian">
    <strong>MARLA</strong> PELHAM<br>Accredited Practising Dietitian
  </div>

  <div class="brand-dot"></div>
  <div class="menu-band"></div>

  <ul class="menu">
    <li class="menu-item" style="left:147px">
      <svg class="menu-icon" viewBox="0 0 30 30"><circle cx="11" cy="9" r="6" fill="#faa54b"/><path d="M1 27c0-7 4-10 10-10s9 3 9 10z" fill="#faa54b"/><circle cx="23" cy="18" r="6" fill="#faa54b" stroke="#2a1613" stroke-width="1.5"/></svg>
      About<br>Us
    </li>
    <li class="menu-item" style="left:274px">
      <svg class="menu-icon" viewBox="0 0 30 30"><path d="M8 3v8a3 3 0 0 0 6 0V3M11 3v24" fill="none" stroke="#faa54b" stroke-width="2.2" stroke-linecap="round"/><path d="M20 27V3c4 2 5 7 5 12h-5" fill="none" stroke="#faa54b" stroke-width="2.2" stroke-linejoin="round" stroke-linecap="round"/></svg>
      Nutrition &amp;<br>Diet<br>Services
    </li>
    <li class="menu-item" style="left:400px">
      <svg class="menu-icon" viewBox="0 0 30 30"><circle cx="15" cy="15" r="12" fill="#faa54b"/><path d="M13 8h4v5h5v4h-5v5h-4v-5H8v-4h5z" fill="#2a1613"/></svg>
      Gastro-<br>Enterology<br>Services
    </li>
    <li class="menu-item" style="left:778px">
      <svg class="menu-icon" viewBox="0 0 30 30"><ellipse cx="12" cy="12" rx="11" ry="8" fill="#faa54b"/><path d="M6 18l-2 6 7-4z" fill="#faa54b"/><ellipse cx="22" cy="19" rx="7" ry="5.5" fill="#faa54b" stroke="#2a1613" stroke-width="1.2"/><path d="M25 23l3 4-6-2z" fill="#faa54b"/></svg>
      Blog<br>&amp; News
    </li>
    <li class="menu-item" style="left:882px">
      <svg class="menu-icon" viewBox="0 0 30 30"><rect x="3" y="7" width="24" height="17" fill="none" stroke="#faa54b" stroke-width="2"/><path d="M3 7l12 10 12-10" fill="none" stroke="#faa54b" stroke-width="2"/></svg>
      Contact<br>Us
    </li>
    <li class="menu-item" style="left:1002px">
      <svg class="menu-icon" viewBox="0 0 30 30"><circle cx="15" cy="15" r="12" fill="#faa54b"/><path d="M10 19l7-9 4 3-7 9z" fill="#2a1613"/></svg>
      Fees &amp;<br>Rebate
    </li>
  </ul>

  <h1 class="brand-name">BRIGHT VALE</h1>
</div>
</body>
</html>
```